"Thornbury Accupuncture" needs a Promotional Card - A6 size

Requirements
Must have
• Bright colours, pictures of happy people, acupuncture-related pictures.

```html
<!DOCTYPE html>
<html lang="en">
<head>
<meta charset="utf-8">
<title>Thornbury Accupuncture – A6 Promotional Card</title>
<link href="https://fonts.googleapis.com/css2?family=Source+Sans+3:wght@300;400;600;700&display=swap" rel="stylesheet">
<style>
  :root{
    --red:#e43e2b;
    --red-deep:#c9301f;
    --ink:#1e1e1e;
    --slate:#2f3f48;
    --band:#3a2a24;
    --stage:#8a8a8a;
    --paper:#ffffff;
    --skin-1:#e9c9a5;
    --skin-2:#c99a72;
    --blush:#f6dcd6;
    --gold:#f0b23a;
  }
  *{box-sizing:border-box;margin:0;padding:0}
  html,body{width:1200px;height:1200px;overflow:hidden}
  body{background:var(--stage);font-family:"Source Sans 3",sans-serif;color:var(--ink)}
  .stage{position:absolute;left:0;top:0;width:1500px;height:1500px;transform:scale(.8);transform-origin:0 0}
  .card{position:absolute;top:248px;width:713px;height:1004px;background:var(--paper);overflow:hidden;box-shadow:0 6px 18px rgba(0,0,0,.35)}
  .card--front{left:27px}
  .card--back{left:761px;width:712px}
  .abs{position:absolute}
  .photo{position:absolute}

  /* front */
  .hero-photo{left:0;top:0;width:713px;height:360px;background:linear-gradient(120deg,var(--skin-2) 0%,var(--skin-1) 45%,#f4e6d8 75%,#fff 100%)}
  .brand{left:395px;top:36px;width:320px;text-align:center;color:var(--red);font-weight:700;font-size:34px;line-height:30px;letter-spacing:.2px}
  .brand-dot{display:block;width:46px;height:46px;border-radius:50%;background:var(--gold);margin:0 auto 12px}
  .hero-title{left:247px;top:205px;color:#fff;font-weight:300;font-size:45px;line-height:56px;white-space:nowrap}
  .section-head{display:flex;align-items:center;gap:18px;font-weight:700;font-size:25px;letter-spacing:.3px}
  .section-head .dot{width:64px;height:36px;display:flex;justify-content:center;align-items:center}
  .section-head .dot i{display:block;width:30px;height:30px;border-radius:50%;background:var(--gold)}
  .front .copy{font-size:21px;line-height:25.8px}
  .about-head{left:28px;top:388px}
  .about-copy{left:60px;top:440px;width:255px}
  .mission-head{left:28px;top:692px}
  .mission-copy{left:60px;top:740px;width:390px}
  .quote-band{left:0;top:845px;width:713px;height:115px;background:var(--band)}
  .quote-strip{left:0;top:960px;width:713px;height:44px;background:var(--blush)}
  .quote-label{left:119px;top:870px;color:#fff;font-size:23px;letter-spacing:.2px}
  .quote-label b{font-weight:700}
  .quote-number{left:119px;top:893px;color:#fff;font-size:47px;font-weight:700;letter-spacing:.5px}
  .quote-icon{left:42px;top:870px}

  /* back */
  .back .copy{font-size:18.6px;line-height:23px}
  .intro{left:46px;top:270px;width:625px}
  .hours-head{left:34px;top:500px}
  .hours{left:68px;top:550px;font-size:21px;line-height:26px;display:grid;grid-template-columns:172px auto}
  .loc-head{left:34px;top:640px}
  .loc{left:68px;top:690px;font-size:23px;line-height:29px}
  .find-head{left:287px;top:640px}
  .social{left:345px;top:688px;display:flex;gap:3px}
  .social i{display:block;width:52px;height:52px;border-radius:50%;background:var(--slate)}
  .social i:nth-child(2){background:var(--red)}
  .contact{left:318px;top:862px;color:#fff;font-size:23px;line-height:38px}
  .contact li{list-style:none;display:flex;align-items:center;gap:12px}
  .contact svg{flex:none}
</style>
</head>
<body>
<div class="stage">

  <!-- FRONT -->
  <section class="card card--front front">
    <div class="photo hero-photo" role="img" aria-label="Practitioner placing acupuncture needles in a client's back"></div>
    <svg class="abs" style="left:0;top:0" width="713" height="1004" viewBox="0 0 713 1004">
      <path d="M0 310 Q200 270 420 340 L713 340 L713 1004 L0 1004 Z" fill="#fff"/>
      <path d="M0 318 Q180 280 370 340 Q200 300 0 365 Z" fill="var(--red)"/>
      <circle cx="563" cy="518" r="222" fill="var(--red)"/>
      <circle cx="578" cy="510" r="200" fill="#fff"/>
    </svg>
    <div class="photo" style="left:383px;top:318px;width:390px;height:390px;border-radius:50%;background:radial-gradient(circle at 50% 45%,#efd2bf 0%,#c9a58a 45%,#7a8a6a 100%)" role="img" aria-label="Smiling senior couple embracing"></div>
    <div class="abs brand"><span class="brand-dot"></span>thornbury<br>accupuncture</div>
    <div class="abs hero-title">Additional Title Here</div>

    <div class="abs section-head about-head"><span class="dot"><i></i></span>ABOUT US</div>
    <p class="abs copy about-copy">Lorem ipsum dolor sit amet, consectetur adipiscing elit. Sed tempus orci turpis, sit amet ultricies tellus aliquet in. Nullam at suscipit nisl, vel interdum est. Vestibulum et placerat ipsum, vitae.</p>

    <div class="abs section-head mission-head"><span class="dot"><i></i></span>OUR MISSION</div>
    <p class="abs copy mission-copy">Lorem ipsum dolor sit amet, consectetur adipiscing elit. Sed tempus orci turpis, sit amet ultricies tellus aliquet in.</p>

    <div class="abs quote-band"></div>
    <div class="abs quote-strip"></div>
    <svg class="abs quote-icon" width="66" height="66" viewBox="0 0 24 24" fill="#fff"><path d="M6.6 10.8a15.1 15.1 0 0 0 6.6 6.6l2.2-2.2a1 1 0 0 1 1-.25 11.4 11.4 0 0 0 3.6.57 1 1 0 0 1 1 1V20a1 1 0 0 1-1 1A17 17 0 0 1 3 4a1 1 0 0 1 1-1h3.5a1 1 0 0 1 1 1c0 1.250.2 2.450.57 3.57a1 1 0 0 1-.25 1z"/></svg>
    <div class="abs quote-label"><b>FREE QUOTE</b> CALL OR TEXT</div>
    <div class="abs quote-number">888-888-8888</div>
  </section>

  <!-- BACK -->
  <section class="card card--back back">
    <svg class="abs" style="left:0;top:0" width="712" height="1004" viewBox="0 0 712 1004">
      <rect width="712" height="130" fill="var(--red)"/>
      <circle cx="129" cy="127" r="112" fill="#fff"/>
      <circle cx="357" cy="127" r="112" fill="#fff"/>
      <circle cx="584" cy="127" r="112" fill="#fff"/>
      <path d="M0 827 Q40 822 70 830 L70 1004 L0 1004 Z" fill="var(--red)"/>
      <path d="M0 885 L0 1004 L712 1004 L712 870 Q520 760 280 830 L100 888 Z" fill="var(--slate)"/>
      <path d="M240 820 Q470 740 712 830 L712 862 Q480 770 260 830 Z" fill="var(--red)"/>
      <rect x="0" y="880" width="90" height="6" fill="#fff"/>
      <circle cx="159" cy="870" r="104" fill="#fff"/>
    </svg>
    <div class="photo" style="left:29px;top:27px;width:200px;height:200px;border-radius:50%;background:radial-gradient(circle at 45% 30%,#f05a3c 0%,#d98a7a 35%,#8a8f98 100%)" role="img" aria-label="Shoulder with highlighted pain area"></div>
    <div class="photo" style="left:257px;top:27px;width:200px;height:200px;border-radius:50%;background:linear-gradient(150deg,#c48c5c 0%,#e9c1aa 50%,#f1cfc1 100%)" role="img" aria-label="Gua sha tool used on a back"></div>
    <div class="photo" style="left:484px;top:27px;width:200px;height:200px;border-radius:50%;background:linear-gradient(160deg,#f3f3f3 0%,#f0cbbd 55%,#e2a694 100%)" role="img" aria-label="Hands massaging skin"></div>

    <p class="abs copy intro">Lorem ipsum dolor sit amet, consectetur adipiscing elit. In iaculis rutrum dignissim. Vestibulum facilisis vulputate cursus. Ut vel nulla eu ante euismod fermentum. Nunc consequat in lectus nec pellentesque. Praesent accumsan accumsan nunc, in condimentum eros cursus et. Vivamus ullamcorper imperdiet porta. Proin interdum sed felis eu viverra. Nam a sollicitudin lectus, a iaculis erat. Aenean ut urna auctor eros pulvinar dictum eget vitae lacus. Suspendisse a dapibus lacus. Integer vel fermentum augue, in mollis tortor. Cras sit amet erat.</p>

    <div class="abs section-head hours-head"><span class="dot"><i></i></span>HOURS</div>
    <div class="abs hours"><span>Monday to Friday</span><span>9:00 AM – 7:00 PM</span><span>Saturday</span><span>9:00 AM – 3:00 PM</span></div>

    <div class="abs section-head loc-head"><span class="dot"><i></i></span>LOCATION</div>
    <div class="abs loc">Unit, Street, City<br>State, Zip Code</div>

    <div class="abs section-head find-head"><span class="dot"><i></i></span>FIND US ON</div>
    <div class="abs social"><i></i><i></i><i></i></div>

    <div class="photo" style="left:63px;top:774px;width:192px;height:192px;border-radius:50%;background:radial-gradient(circle at 50% 40%,#e7c4ad 0%,#b08a72 50%,#e9e6e4 100%)" role="img" aria-label="Portrait of the practitioner"></div>

    <ul class="abs contact">
      <li><svg width="24" height="24" viewBox="0 0 24 24" fill="none" stroke="#fff" stroke-width="1.6"><path d="M6.6 10.8a15.1 15.1 0 0 0 6.6 6.6l2.2-2.2a1 1 0 0 1 1-.25 11.4 11.4 0 0 0 3.6.57 1 1 0 0 1 1 1V20a1 1 0 0 1-1 1A17 17 0 0 1 3 4a1 1 0 0 1 1-1h3.5a1 1 0 0 1 1 1c0 1.250.2 2.450.57 3.57a1 1 0 0 1-.25 1z"/></svg>888-888-8888</li>
      <li><svg width="24" height="24" viewBox="0 0 24 24" fill="none" stroke="#fff" stroke-width="1.6"><rect x="2" y="5" width="20" height="14" rx="1"/><path d="M2 6l10 7 10-7"/></svg>name@email.com</li>
      <li><svg width="24" height="24" viewBox="0 0 24 24" fill="none" stroke="#fff" stroke-width="1.6"><path d="M3 11l9-8 9 8M5 9.5V21h5v-6h4v6h5V9.5"/></svg>domain.com</li>
    </ul>
  </section>

</div>
</body>
</html>
```